Sophisticated, clean website reflecting my feminine, playful side to sell my abstract art,

I need a website no more than 3 pages to showcase my paintings, a little about me and some contact info. I do abstracts so looking for something a little edgy, yet feminine and current.
Updates

Hi there, These are some artists websites that I Iike: Marnelvoss.com (I like how airy it is) peterwallombry.com garethpolvens.com (I like how it scrolls) I'll need a place for a photo ( a headshot-i do not have it yet so I'll need to be able to upload that later) as well as an area for my bio. Also, it's important that I will be able to upload any new photos and descriptions easily so it should be user friendly. Lastly, I like in a sunny place so would like to have this seem upbeat and playful as that is how i like to paint. thanks-I'm trying to upload my photos now -

Target Market(s)

ppl ages 35-70 who want large scale art for their homes

Industry/Entity Type

art

Coding

Coded - Design and coding required

Number of Pages Required

3 page

Colors

Designer to choose colors to be used in the design.

Requirements
Must have
• photos of my art, a place for my bio, be easy to reach me. tasteful-nothing too "in your face" -my clients are pretty high end and organized. They like clean lines
Nice to have
• sophisticated background, muted tones in the back-similar clean font throughout-no cursive
Should not have
• too many dark areas. Too many blocks of color. Too serious.

```html
<!DOCTYPE html>
<html lang="en">
<head>
<meta charset="utf-8">
<title>Clara Wendell Art · Contact</title>
<link rel="stylesheet" href="https://fonts.googleapis.com/css2?family=Playfair+Display:wght@500&family=Poppins:wght@400;500;600&family=Tinos&family=Roboto:wght@400&display=swap">
<style>
:root{
  --ink:#111111;
  --text:#3a3a3a;
  --muted:#5a5a5a;
  --rule:#cfcfcf;
  --field:#b9b9b9;
  --accent:#2f8fc8;
  --footer:#f7f7f7;
  --white:#ffffff;
}
*{box-sizing:border-box;margin:0;padding:0}
html,body{width:1200px;height:884px;overflow:hidden;background:var(--white)}
body{position:relative;font-family:"Poppins",sans-serif;color:var(--text)}
.site-header{position:absolute;left:0;top:0;width:1200px;height:66px;border-bottom:1px solid var(--rule);text-align:center}
.brand{font-family:"Playfair Display",serif;font-weight:500;font-size:36px;line-height:72px;color:var(--ink);letter-spacing:-0.3px}
.main-nav a{position:absolute;top:86px;transform:translateX(-50%);font-size:17px;color:var(--muted);text-decoration:none;letter-spacing:0.2px}
.main-nav a.active{color:var(--ink);font-weight:500}
.contact-title{position:absolute;left:98px;top:172px;font-size:29px;font-weight:400;color:var(--ink)}
.field-label{position:absolute;font-size:14px;color:var(--text)}
.field{position:absolute;border:1px solid var(--field);background:var(--white)}
.captcha{position:absolute;left:349px;top:608px;width:188px;height:47px;border:1px solid #d6d6d6;border-radius:2px;background:#f9f9f9;box-shadow:0 0 3px rgba(0,0,0,.08);font-family:"Roboto",sans-serif}
.captcha-box{position:absolute;left:8px;top:13px;width:17px;height:17px;border:2px solid #c1c1c1;border-radius:2px;background:var(--white)}
.captcha-text{position:absolute;left:33px;top:15px;font-size:9px;color:#222}
.captcha-mark{position:absolute;right:8px;top:7px;width:20px;height:20px;border-radius:50%;background:#a9b9d6}
.captcha-name{position:absolute;right:7px;top:29px;font-size:6px;color:#555}
.captcha-links{position:absolute;right:8px;top:37px;font-size:5px;color:#777}
.submit{position:absolute;left:553px;top:608px;width:130px;height:46px;border:none;background:var(--accent);color:var(--white);font-family:"Poppins",sans-serif;font-weight:600;font-size:15px;letter-spacing:.3px}
.artwork{position:absolute;left:737px;top:182px;width:362px;height:477px;border-radius:4px;background:linear-gradient(160deg,#9a9a96 0%,#2f8aa0 25%,#b8692c 45%,#2b2d2a 65%,#2f6b4a 85%,#d8d4c8 100%)}
.site-footer{position:absolute;left:0;top:737px;width:1200px;height:147px;background:var(--footer)}
.social{position:absolute;top:777px;width:38px;height:38px;border:1.5px solid var(--ink);border-radius:50%;display:flex;align-items:center;justify-content:center;font-size:9px;color:var(--ink);text-decoration:none}
.copyright{position:absolute;left:0;top:835px;width:1200px;text-align:center;font-family:"Tinos",serif;font-size:16px;color:var(--ink)}
</style>
</head>
<body>
<header class="site-header">
  <div class="brand">Clara Wendell Art</div>
</header>
<nav class="main-nav">
  <a class="active" href="#" style="left:313px">HOME</a>
  <a href="#" style="left:477px">ABOUT ME</a>
  <a href="#" style="left:674px">MY PAINTINGS</a>
  <a href="#" style="left:871px">CONTACT</a>
</nav>

<main>
  <h1 class="contact-title">Contact</h1>
  <form>
    <label class="field-label" style="left:99px;top:227px">First Name*</label>
    <div class="field" style="left:100px;top:261px;width:281px;height:48px"></div>
    <label class="field-label" style="left:399px;top:227px">Last Name*</label>
    <div class="field" style="left:400px;top:262px;width:281px;height:48px"></div>
    <label class="field-label" style="left:99px;top:333px">Email Address*</label>
    <div class="field" style="left:100px;top:368px;width:281px;height:48px"></div>
    <label class="field-label" style="left:399px;top:333px">Phone Number*</label>
    <div class="field" style="left:400px;top:368px;width:281px;height:48px"></div>
    <label class="field-label" style="left:99px;top:437px">Message*</label>
    <div class="field" style="left:100px;top:473px;width:582px;height:113px"></div>
    <div class="captcha">
      <span class="captcha-box"></span>
      <span class="captcha-text">I'm not a robot</span>
      <span class="captcha-mark"></span>
      <span class="captcha-name">VerifyBox</span>
      <span class="captcha-links">Privacy - Terms</span>
    </div>
    <button class="submit" type="button">SUBMIT</button>
  </form>
  <div class="artwork" role="img" aria-label="Abstract painting with teal, orange, black and white brushstrokes"></div>
</main>

<footer class="site-footer"></footer>
<a class="social" href="#" style="left:537px">Folio</a>
<a class="social" href="#" style="left:580px">Chirp</a>
<a class="social" href="#" style="left:625px">Lens</a>
<p class="copyright">©Copyright ©2022 Clara Wendell Art. All Rights Reserved.</p>
</body>
</html>
```